Lifecoach needs website design based on a standard Wordpress theme

I need a website for my new lifecoaching business that can be easily implemented in Wordpress, it needs to be compatible with a standard Wordpress theme. So I can place the pictures, texts etc. in a standard theme of Wordpress.

I want the design to be a very good feeling and playfull one, based on my logo.

Target Market(s)

I will coach people to reach their goals and dreams in life.

Industry/Entity Type

Business

Requirements
Must have
• Can be easy implemented in Wordpress.
Nice to have
• Photo's of nature are nice.

```html
<!DOCTYPE html>
<html lang="en">
<head>
<meta charset="utf-8">
<title>Ruben Aalders Lifecoach</title>
<link href="https://fonts.googleapis.com/css2?family=Source+Sans+3:ital,wght@0,400;0,600;0,700;1,400&display=swap" rel="stylesheet">
<style>
:root{
  --blue:#3a9be0;
  --blue-dark:#2a7cc4;
  --blue-nav-active:#2d78b8;
  --sky:#6cb4e2;
  --title:#1d5d93;
  --text:#7a7f86;
  --muted:#9aa0a6;
  --border:#d8dde2;
  --amber:#f2b632;
  --cta:#08aeec;
  --cta-edge:#0a7fbd;
  --footer:#0c4a78;
  --white:#fff;
  --page:#f8fafb;
}
*{box-sizing:border-box;margin:0;padding:0}
html,body{width:933px;height:1200px;overflow:hidden}
body{position:relative;background:var(--page);font-family:"Source Sans 3",sans-serif;color:var(--text)}
.abs{position:absolute}
.top-contact{top:19px;right:124px;display:flex;gap:22px;font-size:8px;color:var(--blue-dark);align-items:center}
.top-contact span{display:flex;align-items:center;gap:6px}
.nav-band{top:51px;left:0;width:933px;height:35px;background:linear-gradient(#4aa8ea,#2e8ad3);z-index:2}
.nav{top:51px;left:476px;height:35px;display:flex;z-index:3}
.nav a{display:flex;align-items:center;justify-content:center;height:35px;color:var(--white);font-size:10px;font-weight:700;text-decoration:none;border-left:1px solid rgba(0,0,0,.15)}
.nav a:last-child{border-right:1px solid rgba(0,0,0,.15)}
.nav a.active{background:var(--blue-nav-active)}
.brand{top:0;left:124px;width:292px;height:109px;background:linear-gradient(#fdfdfd,#ececec);box-shadow:0 2px 4px rgba(0,0,0,.18);z-index:4;display:flex;align-items:center;padding-left:20px;gap:12px}
.brand-mark{width:64px;height:64px;border-radius:50%;background:var(--blue-dark)}
.brand-name{color:var(--title);font-weight:600;font-size:20px;line-height:1.05;letter-spacing:.5px}
.hero{top:86px;left:0;width:933px;height:554px;background:linear-gradient(180deg,#fbf7ef 0%,#fde6c8 45%,#f6c534 72%,#d8b22a 100%)}
.hero-figure{top:120px;left:520px;width:400px;height:520px;background:radial-gradient(ellipse at 45% 40%,#fbe8dc 0%,#f3c8b0 40%,rgba(243,200,176,0) 72%)}
.hero-box{top:228px;left:0;width:454px;height:189px;background:rgba(108,180,226,.92);padding:32px 40px 0 136px;color:var(--white)}
.hero-box h1{font-size:24px;font-weight:700;line-height:32px;margin-bottom:8px}
.hero-box p{font-size:13px;line-height:16px}
.dots{top:474px;left:754px;display:flex;gap:3px}
.dots i{width:8px;height:8px;border-radius:50%;background:#c9d9dd}
.dots i.on{background:var(--blue-dark)}
.card{top:518px;width:218px;height:264px;background:var(--white);border:1px solid var(--border);padding:15px 9px 0}
.card h2{font-size:17px;font-weight:400;color:var(--title);text-align:center;margin-bottom:8px}
.photo{width:197px;height:101px}
.card p{font-size:8.5px;line-height:14.5px;margin-top:16px;padding:0 2px}
.btn{display:inline-flex;align-items:center;justify-content:center;gap:5px;width:80px;height:27px;border:1px solid #c8cdd2;border-radius:14px;background:linear-gradient(#fff,#eceff1);font-size:8.5px;color:var(--muted)}
.card .btn{position:absolute;left:11px;top:213px}
.field{height:27px;border:1px solid var(--amber);margin:0 10px 13px 14px;padding-left:10px;font-size:8px;display:flex;align-items:center;color:#6d7278}
.section-title{font-size:17px;color:var(--title);font-weight:400}
.rule{height:4px;border-top:1px solid #d5d8db;border-bottom:1px solid #d5d8db}
.coach-text{top:862px;left:360px;width:205px;font-size:8.5px;line-height:13.2px}
.coach-text p{margin-bottom:13px}
.avatar{top:852px;left:660px;width:64px;height:64px;border-radius:50%;background:linear-gradient(#7a5340,#c9967c)}
.cta{top:1052px;left:0;width:933px;height:70px;background:var(--cta);border-top:3px solid var(--cta-edge)}
.cta-text{top:1078px;left:130px;font-size:16.5px;font-weight:700;color:var(--white)}
.cta-btn{top:1071px;left:634px;width:178px;height:37px;border-radius:5px;background:linear-gradient(#2fc0f2,#0aa2dc);box-shadow:0 2px 3px rgba(0,0,0,.2);color:var(--white);font-size:12.5px;font-weight:700;display:flex;align-items:center;justify-content:center}
.footer{top:1122px;left:0;width:933px;height:78px;background:var(--footer);color:var(--white)}
.foot-links{top:1140px;left:131px;font-size:8px;font-weight:700;letter-spacing:.3px}
.foot-copy{top:1163px;left:130px;font-size:7.8px}
.social{top:1137px;left:539px;display:flex;gap:9px}
.social i{width:20px;height:20px;border-radius:50%;background:var(--white)}
.foot-contact{top:1138px;left:652px;font-size:8px;font-weight:700;line-height:22px}
.foot-contact div{display:flex;align-items:center;gap:10px}
</style>
</head>
<body>
<div class="abs top-contact">
  <span><svg width="22" height="11" viewBox="0 0 22 11"><path d="M0 3h5M2 6h4M8 1h13v9H8z M8 1l6.5 5L21 1" fill="none" stroke="#4a9ad8" stroke-width="1"/></svg>info@rubenaalders.com</span>
  <span><svg width="11" height="11" viewBox="0 0 12 12"><path d="M3 1l2 3-1 1.5c.8 1.6 1.8 2.6 3.4 3.4L9 8l3 2-1.5 2C5 11.5.5 7 0 1.5z" fill="#4a9ad8"/></svg>+84 912 404 377</span>
</div>
<div class="abs nav-band"></div>
<nav class="abs nav">
  <a class="active" style="width:65px">Home</a>
  <a style="width:66px">About</a>
  <a style="width:66px">Coaching</a>
  <a style="width:72px">Articles</a>
  <a style="width:65px">Contact</a>
</nav>
<header class="abs brand">
  <div class="brand-mark"></div>
  <div class="brand-name">RUBEN AALDERS<br>LIFECOACH</div>
</header>

<section class="abs hero" role="img" aria-label="Sunlit meadow with a woman in a white dress, arms spread wide"></section>
<div class="abs hero-figure"></div>
<div class="abs hero-box">
  <h1>Make your life be what you want it to be!</h1>
  <p>Lorem ipsum dolor sit amet, consectetur adipisic-ing elit, sed do eiusmod tempor incididunt ut labore et dolore magna aliqua.</p>
</div>
<div class="abs dots"><i class="on"></i><i></i><i></i><i></i></div>

<article class="abs card" style="left:124px">
  <h2>What is Life Coaching?</h2>
  <div class="photo" role="img" aria-label="Two women talking in a bright room" style="background:linear-gradient(90deg,#8a7566,#e9e7e3 45%,#f4f2ef)"></div>
  <p>Lorem ipsum dolor sit amet, consectetur adipisic-ing elit, sed do eiusmod tempor incididunt ut labore et dolore magna aliqua.</p>
  <span class="btn">Read More ›</span>
</article>
<article class="abs card" style="left:358px">
  <h2>Life Advices</h2>
  <div class="photo" role="img" aria-label="Man and woman talking outdoors among green trees" style="background:linear-gradient(90deg,#b8c98e,#6f8f3c 50%,#9fb86a)"></div>
  <p>Lorem ipsum dolor sit amet, consectetur adipisic-ing elit, sed do eiusmod tempor incididunt ut labore et dolore magna aliqua.</p>
  <span class="btn">Read More ›</span>
</article>
<article class="abs card" style="left:590px;padding-left:0;padding-right:0">
  <h2>Sign up for Newsletter</h2>
  <p style="margin:0 12px 12px 22px;font-size:8.5px;line-height:14.5px">Lorem ipsum dolor sit amet, consectetur adipisicing elit, sed do eiusmod tempor incidi-dunt ut labore et dolore magna aliqua.</p>
  <div class="field">Your Name</div>
  <div class="field" style="margin-bottom:8px">Your Email</div>
  <p style="margin:0 0 0 22px;font-size:7.5px">*Your email will be held in strictest confidentiality.</p>
  <span class="btn" style="left:19px">Submit Now</span>
</article>

<h2 class="abs section-title" style="top:803px;left:128px">Meet Your Life Coach</h2>
<div class="abs rule" style="top:837px;left:126px;width:437px"></div>
<div class="abs" role="img" aria-label="Portrait of the life coach" style="top:860px;left:126px;width:218px;height:142px;background:linear-gradient(90deg,#c9c3bb,#b88f73 45%,#e8e6e3 80%)"></div>
<div class="abs coach-text">
  <p>Tempor incididunt ut labore et dolore magna aliqua. Ut enim ad minim veniam, quis nostrud exercitation. Lorem ipsum dolor sit amet, con-sectetur adipisicing elit, sed do eiusmod</p>
  <p>Lorem ipsum dolor sit amet, consectetur adipisic-ing elit, sed do eiusmod</p>
</div>
<span class="abs btn" style="top:975px;left:360px">Read More ›</span>

<h2 class="abs section-title" style="top:803px;left:591px">Client Testimonial</h2>
<div class="abs rule" style="top:837px;left:589px;width:219px"></div>
<div class="abs avatar" role="img" aria-label="Client portrait"></div>
<div class="abs" style="top:925px;left:600px;width:186px;text-align:center;font-size:10px">Lena Marsh<br><span style="font-size:8.5px;color:#6d7278">Paris, France</span></div>
<p class="abs" style="top:959px;left:600px;width:190px;font-size:8.5px;line-height:14.5px;font-style:italic;color:var(--muted)">"Lorem ipsum dolor sit amet, consectetur adipi-sicing elit, sed do eiusmod tempor incididunt ut labore et dolore magna aliqua."</p>

<section class="abs cta"></section>
<div class="abs cta-text">Life life to the fullest. Book a Private Coaching Session Now.</div>
<div class="abs cta-btn">Request Coaching Session</div>

<footer class="abs footer"></footer>
<div class="abs foot-links">LINKS &nbsp;| &nbsp;LINKS &nbsp;| &nbsp;LINKS &nbsp;| &nbsp;LINKS</div>
<div class="abs foot-copy">Copyright © 2014. All rights reserved. &nbsp;Company Name. Privacy Policy &nbsp;| &nbsp;Sitemap</div>
<div class="abs social"><i></i><i></i><i></i></div>
<div class="abs foot-contact">
  <div><svg width="14" height="10" viewBox="0 0 14 10"><path d="M0 0h14v10H0z" fill="#2f86c8"/><path d="M0 0l7 5 7-5" fill="none" stroke="#0c4a78"/></svg>hello@rubenaalders.com</div>
  <div><svg width="14" height="12" viewBox="0 0 12 12"><path d="M3 1l2 3-1 1.5c.8 1.6 1.8 2.6 3.4 3.4L9 8l3 2-1.5 2C5 11.5.5 7 0 1.5z" fill="#2f86c8"/></svg>890-12345-67890</div>
</div>
</body>
</html>
```